Consulting Group Needs a Graphic Design

We have created a unique, cyclical process to describe our company's philosophy on parenting to our clients. It is provided in the attached file. At the center of the graphic design, which includes all written words on the page, is an image of a gardener that we really like. We found it through a clipart service, but we are not able to trademark it as our own. We would like to create a similar image which includes the female gardener tending the garden, with a trowel in her hand and a watering can at her side. We want the flowers in her garden to be different, just as every child is unique and different within the same family. For more perspective on our company, please visit www.brookvalecounsel.com.
Updates

Project Deadline Extended
Reason: Some of the designers are getting very close to what we want. Due to some unforeseen circumstances, we were unable to give feedback for a couple of days. We would really appreciate your consideration of our request. We are eager to get the design finished to move forward with our branding strategy, so we will be hyper-focused on the project over the coming days. Thank you, Willowmere Family Advisors

Project Deadline Extended
Reason: We would like to give our first choice designer a chance to create a complementary logo to accompany his submission. We have been in communication with this designer.

Industry/Entity Type

Gardener

```html
<!DOCTYPE html>
<html lang="en">
<head>
<meta charset="utf-8">
<title>Willowmere Family Advisors – Business Card Options</title>
<link href="https://fonts.googleapis.com/css2?family=Jost:wght@400;500;600&display=swap" rel="stylesheet">
<style>
  :root {
    --leaf: #0b9b3c;
    --leaf-dark: #0d6b2e;
    --soil: #6b3d1d;
    --sun: #f4e61c;
    --lime: #d9ec4a;
    --label: #9a9a9a;
    --ink: #3a3a3a;
    --paper: #ffffff;
    --frame: #4a4a4a;
  }
  * { box-sizing: border-box; margin: 0; padding: 0; }
  html, body { width: 1200px; height: 696px; overflow: hidden; background: var(--paper); }
  body { position: relative; font-family: "Jost", "Futura", sans-serif; color: var(--ink); }

  .side-label, .option-label {
    position: absolute; color: var(--label); font-weight: 500; font-size: 19px;
  }
  .side-label { top: 24px; }
  .option-label { left: 29px; }

  .card {
    position: absolute; width: 504px; height: 287px; overflow: hidden;
    border: 1px solid var(--frame);
  }
  .card--green { background: var(--leaf); border-color: var(--leaf); }
  .card--white { background: var(--paper); }
  .card > * { position: absolute; }

  .col-front { left: 133px; }
  .col-back { left: 661px; }
  .row-a { top: 56px; }
  .row-b { top: 385px; }

  /* Illustrations */
  .illustration { border-radius: 10px; }
  .illustration--logo {
    left: 44px; top: 66px; width: 150px; height: 140px;
    background: linear-gradient(160deg, #2fa6e0 0%, #f29a1e 60%, #7a4a23 100%);
  }
  .illustration--garden {
    left: 54px; top: 66px; width: 186px; height: 156px;
    background: linear-gradient(160deg, #2fa6e0 0%, #f29a1e 55%, #2d6e2a 100%);
  }

  /* Front A */
  .brand-name {
    left: 208px; top: 110px; width: 280px;
    color: var(--soil); font-weight: 500; font-size: 30px; line-height: 1.05;
  }
  .web-front {
    left: 0; right: 0; top: 198px; padding-left: 150px; text-align: center;
    color: var(--leaf-dark); font-weight: 600; font-size: 18px;
  }

  /* Front B */
  .method-title {
    left: 0; right: 0; top: 16px; text-align: center;
    color: var(--paper); font-size: 27px; font-weight: 400;
  }
  .method-title sup { font-size: 10px; vertical-align: 14px; }
  .steps { left: 270px; top: 72px; list-style: none; }
  .steps li {
    color: var(--sun); font-size: 16px; line-height: 28px; padding-left: 15px; position: relative;
  }
  .steps li::before {
    content: ""; position: absolute; left: 0; top: 12px; width: 5px; height: 5px;
    border-radius: 50%; background: var(--sun);
  }
  .web-strip {
    left: 0; right: 0; bottom: 0; height: 59px; background: var(--paper);
    display: flex; align-items: center; justify-content: center;
    color: var(--leaf-dark); font-weight: 600; font-size: 18px;
  }

  /* Back */
  .person { left: 30px; }
  .person-name { font-size: 18px; font-weight: 500; line-height: 1.2; }
  .person-role { font-size: 15px; line-height: 1.1; }
  .divider { left: 178px; width: 1px; }
  .contact { left: 205px; font-size: 17px; line-height: 21px; }
  .contact-phone { font-size: 19px; font-weight: 500; }
  .socials { left: 40px; list-style: none; }
  .socials li { display: flex; align-items: center; height: 33px; font-size: 15px; }
  .social-mark { width: 21px; height: 21px; border-radius: 3px; margin-right: 12px; flex: none; }

  .card--green .person { top: 65px; color: var(--paper); }
  .card--green .person-role { color: var(--lime); }
  .card--green .divider { top: 26px; height: 108px; background: rgba(255,255,255,0.45); }
  .card--green .contact { top: 48px; color: var(--paper); }
  .card--green .socials { top: 160px; color: var(--paper); }
  .card--green .social-mark { background: var(--paper); }

  .card--white .person { top: 48px; }
  .card--white .person-name { color: var(--leaf-dark); }
  .card--white .person-role { color: var(--ink); }
  .card--white .divider { top: 22px; height: 81px; background: #bbbbbb; }
  .card--white .contact { top: 26px; color: var(--ink); }
  .firm-band {
    left: 0; right: 0; top: 117px; height: 38px; background: var(--leaf);
    display: flex; align-items: center; justify-content: center;
    color: var(--paper); font-size: 19px; font-weight: 500;
  }
  .card--white .socials { top: 166px; color: var(--ink); }
  .card--white .social-mark { background: var(--leaf); }
</style>
</head>
<body>
  <span class="side-label" style="left:133px">Front</span>
  <span class="side-label" style="left:663px">Back</span>
  <span class="option-label" style="top:159px">Option A</span>
  <span class="option-label" style="top:477px">Option B</span>

  <!-- Option A front -->
  <section class="card card--white col-front row-a">
    <div class="illustration illustration--logo" role="img" aria-label="Illustration of a kneeling gardener with a trowel and watering can beside three small flowers"></div>
    <div class="brand-name">Willowmere Family Advisors, LLC</div>
    <div class="web-front">www.brookvalecounsel.com</div>
  </section>

  <!-- Option A back -->
  <section class="card card--green col-back row-a">
    <div class="person">
      <div class="person-name">Dana Whitfield</div>
      <div class="person-role">CEO</div>
    </div>
    <div class="divider"></div>
    <div class="contact">
      <div class="contact-phone">555-014-2388</div>
      <div>address</div>
      <div>dana@brookvalecounsel.com</div>
    </div>
    <ul class="socials">
      <li><span class="social-mark"></span>www.linkwall.com/willowmereadvisors</li>
      <li><span class="social-mark"></span>www.chirpline.com/danawhitfield</li>
      <li><span class="social-mark"></span>www.willowmereadvisorsblog.com</li>
    </ul>
  </section>

  <!-- Option B front -->
  <section class="card card--green col-front row-b">
    <h1 class="method-title">The Willowmere Growth Method<sup>TM</sup></h1>
    <div class="illustration illustration--garden" role="img" aria-label="Illustration of a kneeling gardener with a trowel and watering can tending a bed of different flowers"></div>
    <ul class="steps">
      <li>Plant with purpose</li>
      <li>Nurture</li>
      <li>Enrich the soil</li>
      <li>Prune as needed</li>
      <li>Measure progress</li>
    </ul>
    <div class="web-strip">www.brookvalecounsel.com</div>
  </section>

  <!-- Option B back -->
  <section class="card card--white col-back row-b">
    <div class="person">
      <div class="person-name">Dana Whitfield</div>
      <div class="person-role">CEO</div>
    </div>
    <div class="divider"></div>
    <div class="contact">
      <div class="contact-phone">555-014-2388</div>
      <div>address</div>
      <div>dana@brookvalecounsel.com</div>
    </div>
    <div class="firm-band">Willowmere Family Advisors, LLC</div>
    <ul class="socials">
      <li><span class="social-mark"></span>www.linkwall.com/willowmereadvisors</li>
      <li><span class="social-mark"></span>www.chirpline.com/danawhitfield</li>
      <li><span class="social-mark"></span>www.willowmereadvisorsblog.com</li>
    </ul>
  </section>
</body>
</html>
```